KLV Plant Services

We are a heavy diesel mechanical business with additional air con certificates, remapping engine rebuilt

Contact Information for Business Card

Company Name, Director Name, Managing Director, Contact details, email and website

Font styles to use
Serif
Script

```html
<!DOCTYPE html>
<html lang="en">
<head>
<meta charset="utf-8">
<title>KLV Plant Services – Business Card</title>
<link rel="stylesheet" href="https://fonts.googleapis.com/css2?family=Michroma&family=Open+Sans:wght@400;600&display=swap">
<style>
  :root {
    --page-bg: #e9e7e4;
    --navy-light: #201b6e;
    --navy-dark: #050322;
    --navy-ink: #24206e;
    --accent-violet: #5550c4;
    --ink-dark: #1c1c1c;
    --ink-grey: #4a4a4a;
    --card-white: #ffffff;
    --card-shade: #f1f1f1;
  }
  * { box-sizing: border-box; margin: 0; padding: 0; }
  html, body {
    width: 1200px; height: 900px; overflow: hidden;
    background: var(--page-bg);
  }
  .canvas {
    position: relative; width: 1200px; height: 900px;
    display: flex; flex-direction: column; align-items: center;
    justify-content: center; gap: 40px;
  }
  .card {
    position: relative; width: 700px; height: 400px;
    border-radius: 34px; overflow: hidden;
    box-shadow: 0 10px 28px rgba(0,0,0,0.18);
  }

  /* Back side */
  .card-back {
    background: radial-gradient(ellipse at 35% 55%, var(--navy-light) 0%, #120e4a 45%, var(--navy-dark) 100%);
  }
  .card-back .web-address {
    position: absolute; top: 42px; right: 48px;
    font-family: "Open Sans", sans-serif; font-weight: 600;
    font-size: 17px; letter-spacing: 6px; color: #e8e8f4;
  }
  .card-back .web-address .accent { color: var(--accent-violet); }
  .card-back .brand {
    position: absolute; left: 96px; bottom: 96px;
    display: flex; align-items: center; gap: 22px;
  }
  .brand-dot {
    width: 54px; height: 54px; border-radius: 50%;
    border: 5px solid currentColor; flex: none;
  }
  .brand-name {
    font-family: "Michroma", sans-serif; font-size: 30px;
    line-height: 1.2;
  }
  .card-back .brand { color: #f4f4f8; }

  /* Front side */
  .card-front {
    background: linear-gradient(160deg, var(--card-white) 0%, var(--card-white) 55%, var(--card-shade) 100%);
  }
  .contact-block {
    position: absolute; left: 56px; top: 96px;
    font-family: "Open Sans", sans-serif;
  }
  .person-name {
    font-family: "Michroma", sans-serif; font-size: 24px;
    color: var(--ink-dark); letter-spacing: 1px;
  }
  .person-role {
    margin-top: 4px; font-size: 17px; color: var(--navy-ink);
  }
  .role-rule {
    width: 120px; height: 2px; background: var(--navy-ink);
    margin: 10px 0 0 24px;
  }
  .contact-list {
    list-style: none; margin-top: 40px; margin-left: 40px;
    font-size: 17px; color: var(--ink-grey); line-height: 1.45;
  }
  .contact-list li { display: flex; align-items: flex-start; gap: 12px; }
  .contact-list svg {
    width: 18px; height: 18px; margin-top: 4px; flex: none;
    fill: none; stroke: var(--navy-ink); stroke-width: 2;
  }
  .card-front .brand {
    position: absolute; right: 56px; top: 150px;
    display: flex; align-items: center; gap: 18px;
    color: var(--navy-ink);
  }
  .card-front .brand-name { font-size: 26px; }
</style>
</head>
<body>
<main class="canvas">

  <section class="card card-back" aria-label="Business card back">
    <p class="web-address"><span class="accent">www</span>.klvplantservices<span class="accent">.net</span></p>
    <div class="brand">
      <span class="brand-dot" aria-hidden="true"></span>
      <span class="brand-name">KLV<br>Plant Services</span>
    </div>
  </section>

  <section class="card card-front" aria-label="Business card front">
    <div class="contact-block">
      <h1 class="person-name">DANIEL MORROW</h1>
      <p class="person-role">Managing Director</p>
      <div class="role-rule"></div>
      <ul class="contact-list">
        <li>
          <svg viewBox="0 0 24 24" aria-hidden="true"><path d="M5 3h4l2 5-2.5 1.5a11 11 0 0 0 6 6L16 13l5 2v4a2 2 0 0 1-2 2A16 16 0 0 1 3 5a2 2 0 0 1 2-2z"/></svg>
          <span>0400 562 918</span>
        </li>
        <li>
          <svg viewBox="0 0 24 24" aria-hidden="true"><rect x="3" y="5" width="18" height="14" rx="1"/><path d="M3 6l9 7 9-7"/></svg>
          <span>admin@klvplantservices.net</span>
        </li>
        <li>
          <svg viewBox="0 0 24 24" aria-hidden="true"><circle cx="12" cy="12" r="9"/><path d="M3 12h18M12 3c3 3 3 15 0 18M12 3c-3 3-3 15 0 18"/></svg>
          <span>www.klvplantservices.net</span>
        </li>
        <li>
          <svg viewBox="0 0 24 24" aria-hidden="true"><path d="M12 22s7-7 7-12a7 7 0 0 0-14 0c0 5 7 12 7 12z"/><circle cx="12" cy="10" r="2.5"/></svg>
          <span>48 Harlow Road, Carrow Park<br>WA 6090, Australia</span>
        </li>
      </ul>
    </div>
    <div class="brand">
      <span class="brand-dot" aria-hidden="true"></span>
      <span class="brand-name">KLV<br>Plant Services</span>
    </div>
  </section>

</main>
</body>
</html>
```